Consulting company business cards

We have a base design, but would be willing to update. We have a new logo/"tag" that needs to be added. Current business card design is attached for reference into our "style."

Industry/Entity Type

Business

Contact Information for Business Card

Should contain name and title, office number, mobile number if appropriate, e-mail, website, physical address, and company logo.

Font styles to use
Other font styles liked:
• See current card design on KorvandBCard

Colors
0455a3
85acd3
aaaaaa

Requirements
Must have
• Our colors are navy blue, gray, and a lighter blue
Nice to have
• Design that I can easily drop in new names/titles as we hire employees.

```html
<!DOCTYPE html>
<html lang="en">
<head>
<meta charset="utf-8">
<title>Brenlow Business Card – Helena Korvand</title>
<link rel="stylesheet" href="https://fonts.googleapis.com/css2?family=PT+Sans:wght@400;700&display=swap">
<style>
  :root {
    --navy: #0455a3;
    --ink: #1f3f5c;
    --light-blue: #85acd3;
    --gray: #aaaaaa;
    --frost: #eef2f5;
    --white: #ffffff;
    --page: #e4e6e8;
  }
  html, body {
    margin: 0;
    padding: 0;
    width: 1200px;
    height: 969px;
    overflow: hidden;
    background: var(--page);
    font-family: "PT Sans", Arial, sans-serif;
  }
  .card {
    position: absolute;
    left: 100px;
    top: 200px;
    width: 1000px;
    height: 569px;
    border-radius: 34px;
    overflow: hidden;
    background: var(--frost);
    box-shadow: 0 6px 24px rgba(0, 0, 0, 0.12);
  }
  .card__artwork {
    position: absolute;
    inset: 0;
    width: 100%;
    height: 100%;
  }
  .contact {
    position: absolute;
    left: 48px;
    top: 58px;
    color: var(--white);
  }
  .contact__name {
    margin: 0;
    font-size: 29px;
    font-weight: 700;
    letter-spacing: 0.5px;
    color: #dde8f2;
  }
  .contact__title {
    margin: 4px 0 0;
    font-size: 25px;
    font-weight: 400;
  }
  .contact__address {
    margin: 118px 0 0;
    font-style: normal;
    font-size: 22px;
    line-height: 34px;
  }
  .contact__lines {
    margin: 24px 0 0;
    padding: 0;
    list-style: none;
    font-size: 22px;
    line-height: 35px;
  }
  .contact__lines .muted { color: #f2dbe4; }
  .brand {
    position: absolute;
    left: 604px;
    top: 400px;
    color: var(--ink);
  }
  .brand__row {
    display: flex;
    align-items: center;
    gap: 14px;
  }
  .brand__name {
    font-size: 66px;
    font-weight: 700;
    letter-spacing: 6px;
    line-height: 1;
  }
  .brand__dot {
    width: 46px;
    height: 46px;
    border-radius: 50%;
    background: var(--ink);
  }
  .brand__tag {
    margin-top: 8px;
    font-size: 17px;
    letter-spacing: 2.4px;
    color: var(--ink);
  }
</style>
</head>
<body>
  <main class="card">
    <svg class="card__artwork" viewBox="0 0 1000 569" role="img" aria-label="Illustration of a dog's head in profile in soft blue tones">
      <defs>
        <linearGradient id="artwork-tone" x1="0" y1="0" x2="1" y2="0.3">
          <stop offset="0" stop-color="#5f93bf"/>
          <stop offset="0.38" stop-color="#8db2d2"/>
          <stop offset="0.62" stop-color="#dfe7ee"/>
          <stop offset="1" stop-color="#eef2f5"/>
        </linearGradient>
      </defs>
      <rect width="1000" height="569" fill="url(#artwork-tone)"/>
    </svg>

    <section class="contact">
      <h1 class="contact__name">HELENAKORVAND</h1>
      <p class="contact__title">Office Manager</p>
      <address class="contact__address">
        1187 E 54th ST<br>
        Lakeport<br>
        Ohio 45120
      </address>
      <ul class="contact__lines">
        <li>O 555.014.2910</li>
        <li>F 555.014.2971</li>
        <li class="muted">hkorvand@brenlowtech.com</li>
        <li class="muted">www.brenlowtech.com</li>
      </ul>
    </section>

    <div class="brand">
      <div class="brand__row">
        <span class="brand__name">BRENLOW</span>
        <span class="brand__dot"></span>
      </div>
      <div class="brand__tag">A CLOUD CONSULTING COMPANY</div>
    </div>
  </main>
</body>
</html>
```